Velvet Pressings Techno Label Business Card

I'm looking for a very clean business card for my Velvet Pressings music label. The label focusses on techno music. The card should include:

• my name : Tomas Brandt as "Founder & CEO"
• email address: tomas@velvet-pressings.example
• web: www.velvet-pressings.example
• facebook logo + /velvetpress
• twitter logo + /velvetpress
• soundcloud logo + /velvetpressings

Feel free to include your ideas! I'm looking forward to discuss about it.

Tomas

Industry/Entity Type

Business

Contact Information for Business Card

I don't like glossy cards. Prefer matt.

Requirements
Nice to have
• Maybe on one side the complete logo, other side just the icon.
Should not have
• Flashy stuff. Must be clean and business like style.

```html
<!DOCTYPE html>
<html lang="en">
<head>
<meta charset="utf-8">
<title>Velvet Pressings – Business Card</title>
<link rel="stylesheet" href="https://fonts.googleapis.com/css2?family=Arimo:wght@700&family=Montserrat:wght@400;500&display=swap">
<style>
  :root {
    --backdrop: #e9e9e9;
    --card: #fbfbfb;
    --card-shade: #f4f4f4;
    --accent: #ee6a1c;
    --ink: #6f6f6f;
    --ink-soft: #8a8a8a;
    --rule: #dedede;
  }
  * { margin: 0; padding: 0; box-sizing: border-box; }
  html, body {
    width: 1200px; height: 726px; overflow: hidden;
    background: var(--backdrop);
  }
  .canvas {
    position: relative; width: 1200px; height: 726px;
    display: flex; align-items: center; justify-content: center; gap: 60px;
  }
  .card {
    position: relative; width: 525px; height: 300px;
    background: var(--card);
    box-shadow: 0 2px 10px rgba(0,0,0,0.08);
    overflow: hidden;
  }

  /* Front: wordmark */
  .card--front {
    display: flex; align-items: center; justify-content: center; gap: 16px;
  }
  .wordmark-dot {
    width: 26px; height: 26px; border-radius: 50%;
    background: var(--accent); flex: none;
  }
  .wordmark {
    font-family: "Arimo", Arial, sans-serif; font-weight: 700;
    font-size: 40px; letter-spacing: -0.5px;
    color: var(--accent); white-space: nowrap;
  }

  /* Back: contact details */
  .card--back::before,
  .card--back::after {
    content: ""; position: absolute; left: 0; right: 0; height: 9px;
    background: var(--accent);
  }
  .card--back::before { top: 0; }
  .card--back::after { bottom: 0; }

  .brand-panel {
    position: absolute; left: 0; top: 9px; bottom: 9px; width: 260px;
    background: var(--card-shade);
    border-right: 1px solid var(--rule);
    display: flex; flex-direction: column; align-items: center; justify-content: center; gap: 14px;
  }
  .brand-panel .wordmark-dot { width: 64px; height: 64px; }
  .brand-panel .wordmark { font-size: 22px; letter-spacing: 0; }

  .contact-panel {
    position: absolute; left: 260px; right: 0; top: 9px; bottom: 9px;
    padding: 30px 20px 0 26px;
    font-family: "Montserrat", Arial, sans-serif;
  }
  .person-name {
    font-size: 19px; font-weight: 400; color: var(--accent); letter-spacing: 0.3px;
  }
  .person-title {
    margin-top: 4px; font-size: 11px; color: var(--ink-soft); letter-spacing: 0.3px;
  }
  .contact-list {
    position: absolute; left: 26px; right: 16px; bottom: 28px;
    list-style: none; display: flex; flex-direction: column; gap: 7px;
  }
  .contact-item {
    display: flex; align-items: center; gap: 9px;
    font-size: 10.5px; font-weight: 500; color: var(--ink);
    white-space: nowrap;
  }
  .contact-icon { width: 11px; height: 11px; flex: none; }
  .social-dot {
    width: 11px; height: 11px; flex: none; border-radius: 50%;
    background: var(--accent);
  }
  .contact-divider {
    height: 1px; background: var(--rule); margin: 3px 0;
  }
</style>
</head>
<body>
<main class="canvas">
  <section class="card card--front" aria-label="Card front">
    <span class="wordmark-dot"></span>
    <span class="wordmark">Velvet Pressings</span>
  </section>

  <section class="card card--back" aria-label="Card back">
    <div class="brand-panel">
      <span class="wordmark-dot"></span>
      <span class="wordmark">Velvet Pressings</span>
    </div>
    <div class="contact-panel">
      <p class="person-name">Tomas Brandt</p>
      <p class="person-title">Founder &amp; CEO</p>
      <ul class="contact-list">
        <li class="contact-item">
          <svg class="contact-icon" viewBox="0 0 12 12" aria-hidden="true">
            <rect x="0.5" y="2" width="11" height="8" fill="var(--accent)"/>
            <path d="M0.5 2 L6 6.5 L11.5 2" fill="none" stroke="#fff" stroke-width="1"/>
          </svg>
          tomas@velvet-pressings.example
        </li>
        <li class="contact-item">
          <svg class="contact-icon" viewBox="0 0 12 12" aria-hidden="true">
            <circle cx="6" cy="6" r="5.5" fill="var(--accent)"/>
            <path d="M0.5 6 H11.5 M6 0.5 V11.5" stroke="#fff" stroke-width="0.9"/>
            <ellipse cx="6" cy="6" rx="2.4" ry="5.5" fill="none" stroke="#fff" stroke-width="0.9"/>
          </svg>
          www.velvet-pressings.example
        </li>
        <li class="contact-divider" aria-hidden="true"></li>
        <li class="contact-item"><span class="social-dot" aria-hidden="true"></span>/velvetpress</li>
        <li class="contact-item"><span class="social-dot" aria-hidden="true"></span>/velvetpress</li>
        <li class="contact-item"><span class="social-dot" aria-hidden="true"></span>/velvetpressings</li>
      </ul>
    </div>
  </section>
</main>
</body>
</html>
```